Flat bootstrap design for existing site

I'm looking for a modern flat design based around an existing logo. This has to be a custom design (no external templates), and implemented into a bootstrap framework.

The logo is attached as 2 versions - choose whichever you want, that flows better with whatever design you choose.

Added screenshots of the existing site (currently using the default bootstrap layouts). Please make your designs around those pages in the screenshots (i.e. the homepage only has the postal code input and the header). The active page has 3 screenshots, because I wanted to illustrate the other states that would be visible (in the table rows).

This is a moving/junk removal website, just for some context.

Here's some example websites (flat designs) that I like, just to give you an idea of what I'm after.

https://www.plimvora.com/
https://dacklow.com/
https://trevanu.com/
https://quobrintal.com/en/

Coding

Coded - Design and coding required

Number of Pages Required

5+ page

Colors

Designer to choose colors to be used in the design.

Requirements
Must have
• It must be a modern/simple flat design, that is built around the existing logo (attached).
• It has to be implemented using bootstrap.

```html
<!DOCTYPE html>
<html lang="en">
<head>
<meta charset="utf-8">
<title>Haulro – Booking Details</title>
<link href="https://fonts.googleapis.com/css2?family=Roboto:wght@400;500;700&display=swap" rel="stylesheet">
<style>
:root{
  --brand:#4bc9f5;
  --brand-dark:#3db8e2;
  --page:#f7f7f7;
  --card:#ffffff;
  --line:#e3e3e3;
  --text:#666666;
  --muted:#8a8a8a;
  --alert:#8ddcf5;
  --table-head:#8a8a8a;
  --status:#6b6b6b;
  --footer:#5c5c5c;
  --white:#ffffff;
}
*{box-sizing:border-box;margin:0;padding:0}
html,body{width:1200px;height:1089px;overflow:hidden}
body{position:relative;background:var(--page);font-family:'Roboto',sans-serif;color:var(--text)}
.site-header{position:absolute;left:0;top:0;width:1200px;height:88px;background:var(--brand)}
.brand{position:absolute;left:86px;top:26px;display:flex;align-items:center;gap:10px;color:var(--white);font-weight:700;font-size:32px;letter-spacing:1px}
.brand-dot{width:26px;height:26px;border-radius:50%;background:var(--white)}
.main-nav{position:absolute;top:0;left:0;height:88px;width:1200px}
.nav-item{position:absolute;top:0;height:88px;line-height:86px;color:var(--white);font-size:12.5px;font-weight:500;text-decoration:none}
.nav-item.active{background:var(--brand-dark);padding:0 27px}
.caret{position:absolute;left:1099px;top:41px}
.booking-card{position:absolute;left:86px;top:150px;width:1028px;height:343px;background:var(--card);border:1px solid var(--line);border-radius:3px}
.card-title{height:63px;line-height:64px;padding-left:17px;font-size:15.5px;font-weight:500;border-bottom:1px solid #eeeeee}
.field-label{position:absolute;font-size:14px;font-weight:500}
.input{position:absolute;height:41px;border:1px solid var(--line);border-radius:3px;font-size:12.5px;padding-left:13px;line-height:40px;color:var(--text);background:var(--white)}
.input-addon{position:absolute;right:0;top:0;width:39px;height:39px;border-left:1px solid var(--line);background:#f5f5f5;display:flex;align-items:center;justify-content:center}
.textarea{line-height:1;padding-top:13px;height:62px}
.btn-update{position:absolute;left:16px;top:279px;width:106px;height:39px;background:var(--brand);color:var(--white);border-radius:3px;font-size:14px;font-weight:500;text-align:center;line-height:39px}
.section-title{position:absolute;left:86px;top:533px;font-size:15.5px;font-weight:500}
.notice{position:absolute;left:86px;top:567px;width:1028px;height:53px;background:var(--alert);border-radius:3px;color:var(--white);font-size:12.5px;font-weight:500;line-height:53px;padding-left:22px}
.drivers-table{position:absolute;left:86px;top:655px;width:1028px;border-collapse:collapse;border:1px solid var(--line);background:var(--card)}
.drivers-table th{background:var(--table-head);color:var(--white);height:53px;font-size:12.5px;font-weight:500;text-align:left;padding-left:25px;border-right:1px solid #9d9d9d;width:20%}
.drivers-table td{height:63px;font-size:14px;color:var(--muted);padding-left:27px;border-right:1px solid var(--line);border-top:1px solid var(--line)}
.drivers-table th:last-child,.drivers-table td:last-child{border-right:none}
.drivers-table td.pickup{text-align:center;padding-left:0}
.drivers-table td.action{text-align:center;padding-left:0}
.status{display:inline-block;width:127px;height:33px;line-height:33px;background:var(--status);color:var(--white);font-size:12px;font-weight:500;border-radius:2px}
.site-footer{position:absolute;left:0;top:1020px;width:1200px;height:69px;background:var(--footer)}
.copyright{position:absolute;left:86px;top:26px;color:var(--white);font-size:12.5px;font-weight:500}
.social{position:absolute;left:942px;top:19px;display:flex;gap:5px}
.social span{width:30px;height:30px;border:1.5px solid var(--white);border-radius:50%}
</style>
</head>
<body>
<header class="site-header">
  <div class="brand"><span class="brand-dot"></span>HAULRO</div>
  <nav class="main-nav">
    <a class="nav-item" style="left:545px">BOOK</a>
    <a class="nav-item" style="left:636px">HOW IT WORKS</a>
    <a class="nav-item active" style="left:757px;width:161px">BECOME A DRIVER</a>
    <a class="nav-item" style="left:950px">maren@tolvexa.com</a>
    <svg class="caret" width="9" height="6" viewBox="0 0 9 6"><path d="M0 0h9L4.5 5z" fill="#fff"/></svg>
  </nav>
</header>

<section class="booking-card">
  <h2 class="card-title">BOOKING DETAILS</h2>
  <label class="field-label" style="left:18px;top:79px">Package Selected :</label>
  <div class="input" style="left:16px;top:106px;width:484px">Package 1
    <span class="input-addon"><svg width="8" height="12" viewBox="0 0 8 12"><path d="M0 5h8L4 0zM0 7h8l-4 5z" fill="#555"/></svg></span>
  </div>
  <label class="field-label" style="left:531px;top:79px">Pick-up time selected :</label>
  <div class="input" style="left:529px;top:106px;width:485px">July 18 at 0:13 am
    <span class="input-addon"><svg width="12" height="12" viewBox="0 0 12 12"><rect x="0.5" y="1.5" width="11" height="10" fill="none" stroke="#555"/><path d="M0.5 4h11M3 0v3M9 0v3M3 6h1M6 6h1M9 6h1M3 8.5h1M6 8.5h1M9 8.5h1" stroke="#555"/></svg></span>
  </div>
  <label class="field-label" style="left:18px;top:172px">Description :</label>
  <div class="input textarea" style="left:16px;top:199px;width:993px">1 Large Stove</div>
  <div class="btn-update">UPDATE</div>
</section>

<h2 class="section-title">DRIVERS IN YOUR AREA</h2>
<div class="notice">Please stey on this page and be patient,while we contact the drivers and find your one ASAP.</div>

<table class="drivers-table">
  <thead><tr><th>NAME</th><th>DISTANCE (KM)</th><th>AGREED PICK-UP TIME</th><th></th><th></th></tr></thead>
  <tbody>
    <tr><td>Dale Fenwick</td><td>4.04km away</td><td class="pickup">-</td><td></td><td class="action"><span class="status">PENDING</span></td></tr>
    <tr><td>Ronan Pell</td><td>5.7km away</td><td class="pickup">-</td><td></td><td class="action"><span class="status">PENDING</span></td></tr>
    <tr><td>Arlo Brisket</td><td>11.13km away</td><td class="pickup">-</td><td></td><td class="action"><span class="status">PENDING</span></td></tr>
    <tr><td>Milo Drayden</td><td>11.91km away</td><td class="pickup">-</td><td></td><td class="action"><span class="status">PENDING</span></td></tr>
  </tbody>
</table>

<footer class="site-footer">
  <p class="copyright">© Copyright 2017 Haulro.All Rights Reserved.</p>
  <div class="social" aria-label="Social links"><span></span><span></span><span></span><span></span><span></span></div>
</footer>
</body>
</html>
```